UX - Need some screens design for a Skill Assessment Application

I am building an app to carry out skill assessments. Depending on how the assessment is configured, it may have one or more parts
1. Question based assessment (Multiple Choice, True False, Fill in the blanks"
2. Endorsement by two colleagues - A screen that allows user to pick colleagues based on search and shows the status of pending requests
3. A written submission - a page that explains the format of the submission and a file upload
As each assessment can be configured with or without any of the steps, the assessment UI must be such that these areas get hidden/displayed based on configuration.
Colour codes to be used can be #0e78bb and #ffffff
There will also be a start screen (instructions) and an end screen (results)
Target Market(s)
Enterprise software
Number of Pages Required
4 page

```html
<!DOCTYPE html>
<html lang="en">
<head>
<meta charset="utf-8">
<title>Submissions</title>
<link href="https://fonts.googleapis.com/css2?family=Inter:wght@400;500;600&display=swap" rel="stylesheet">
<style>
  :root {
    --brand: #0e78bb;
    --header-bg: #0654a9;
    --white: #ffffff;
    --ink: #222831;
    --ink-soft: #444a52;
    --muted: #5f6368;
    --line: #dfe2e6;
    --head-row: #f6f7f9;
    --pending-bg: #e7f2fc;
    --pending-ink: #0b63a8;
    --approved-bg: #d7f5ef;
    --approved-ink: #169a80;
    --nav-ink: #d3e2f4;
    --disabled: #c5c9ce;
  }
  * { box-sizing: border-box; margin: 0; padding: 0; }
  html, body { width: 1200px; height: 686px; overflow: hidden; background: var(--white); }
  body { font-family: "Inter", Arial, sans-serif; color: var(--ink); }
  .stage { width: 1400px; height: 800px; position: relative; transform: scale(0.857143); transform-origin: 0 0; }

  .topbar { position: absolute; left: 0; top: 0; width: 1400px; height: 50px; background: var(--header-bg); }
  .brand { position: absolute; left: 66px; top: 13px; display: flex; align-items: center; gap: 17px; color: var(--white); font-size: 17px; font-weight: 500; }
  .brand-dot { width: 24px; height: 24px; border-radius: 50%; background: var(--white); }
  .nav { position: absolute; top: 0; height: 50px; display: flex; align-items: center; font-size: 14px; color: var(--nav-ink); }
  .nav a { position: absolute; white-space: nowrap; color: inherit; text-decoration: none; }
  .nav a.active { color: var(--white); font-weight: 600; }
  .avatar { position: absolute; left: 1285px; top: 9px; width: 32px; height: 32px; border-radius: 50%; background: radial-gradient(circle at 50% 40%, #b88a78, #3d2f35); }
  .caret { position: absolute; left: 1323px; top: 19px; }

  .crumb { position: absolute; left: 83px; top: 78px; font-size: 13px; color: var(--ink-soft); }
  .title { position: absolute; left: 83px; top: 110px; font-size: 24px; font-weight: 600; color: var(--ink); }
  .subtitle { position: absolute; left: 83px; top: 150px; font-size: 16px; color: var(--muted); }
  .btn-upload { position: absolute; left: 1124px; top: 122px; width: 173px; height: 36px; border-radius: 3px; background: var(--brand); color: var(--white); font-size: 13px; font-weight: 500; display: flex; align-items: center; justify-content: center; gap: 8px; }

  .tabs { position: absolute; left: 83px; top: 185px; width: 1234px; height: 46px; border-bottom: 1px solid var(--line); }
  .tab { position: absolute; top: 10px; font-size: 16px; color: var(--muted); }
  .tab.active { color: var(--brand); }
  .tab-underline { position: absolute; left: 0; top: 44px; width: 114px; height: 2px; background: var(--brand); }
  .refresh { position: absolute; right: 0; top: 11px; display: flex; align-items: center; gap: 10px; font-size: 14px; font-weight: 500; color: var(--brand); }

  .table { position: absolute; left: 83px; top: 268px; width: 1234px; height: 327px; border: 1px solid var(--line); border-radius: 4px; overflow: hidden; }
  .row { position: absolute; left: 0; width: 100%; border-bottom: 1px solid var(--line); font-size: 14px; }
  .row.head { top: 0; height: 50px; background: var(--head-row); font-weight: 600; color: var(--ink-soft); }
  .row.item { height: 71px; color: var(--muted); }
  .cell { position: absolute; top: 50%; transform: translateY(-50%); white-space: nowrap; }
  .c-name { left: 19px; }
  .row.item .c-name { color: var(--ink); font-weight: 500; }
  .c-date { left: 338px; }
  .c-format { left: 508px; }
  .c-cat { left: 670px; }
  .c-status { left: 983px; }
  .badge { display: inline-block; height: 27px; line-height: 27px; padding: 0 12px; border-radius: 14px; font-size: 13px; font-weight: 500; }
  .badge.pending { background: var(--pending-bg); color: var(--pending-ink); }
  .badge.approved { background: var(--approved-bg); color: var(--approved-ink); }
  .btn-view { left: 1150px; width: 63px; height: 36px; border: 1px solid var(--brand); border-radius: 3px; color: var(--brand); font-size: 13px; display: flex; align-items: center; justify-content: center; background: var(--white); }
  .more { left: 1179px; }

  .pager { position: absolute; left: 0; top: 262px; width: 100%; height: 64px; }
  .page-btn { position: absolute; top: 14px; height: 36px; border: 1px solid var(--line); border-radius: 3px; font-size: 13px; color: var(--disabled); display: flex; align-items: center; justify-content: center; gap: 4px; }
  .page-btn.current { background: var(--brand); border-color: var(--brand); color: var(--white); font-size: 16px; }
</style>
</head>
<body>
<div class="stage">
  <header class="topbar">
    <div class="brand"><span class="brand-dot"></span><span>Korvanta</span></div>
    <nav class="nav">
      <a style="left:877px">Assessments</a>
      <a style="left:989px">Endorsement</a>
      <a class="active" style="left:1101px">Submissions</a>
      <a style="left:1213px">Results</a>
    </nav>
    <div class="avatar" role="img" aria-label="User profile photo"></div>
    <svg class="caret" width="12" height="12" viewBox="0 0 12 12"><path d="M2 4l4 4 4-4" fill="none" stroke="#ffffff" stroke-width="1.6" stroke-linecap="round" stroke-linejoin="round"/></svg>
  </header>

  <div class="crumb">Submissions &nbsp;/</div>
  <h1 class="title">Submissions</h1>
  <p class="subtitle">Here are the complete details of assessments.</p>
  <div class="btn-upload">
    <svg width="15" height="15" viewBox="0 0 16 16"><path d="M8 10V2M5 5l3-3 3 3M2 9v4.5h12V9" fill="none" stroke="#ffffff" stroke-width="1.5" stroke-linecap="round" stroke-linejoin="round"/></svg>
    Upload Documents
  </div>

  <div class="tabs">
    <span class="tab active" style="left:20px">All (3)</span>
    <span class="tab" style="left:189px">Pending (2)</span>
    <span class="tab-underline"></span>
    <span class="refresh">
      <svg width="16" height="16" viewBox="0 0 16 16"><path d="M3.2 5.5A5.5 5.5 0 1 1 2.5 9" fill="none" stroke="#0e78bb" stroke-width="1.7" stroke-linecap="round"/><path d="M2.5 2.5v3.3h3.3" fill="none" stroke="#0e78bb" stroke-width="1.7" stroke-linecap="round" stroke-linejoin="round"/></svg>
      Refresh
    </span>
  </div>

  <section class="table">
    <div class="row head">
      <span class="cell c-name">File Name</span>
      <span class="cell c-date">Upload Date</span>
      <span class="cell c-format">File Format</span>
      <span class="cell c-cat">Document Category</span>
      <span class="cell c-status">Status</span>
    </div>
    <div class="row item" style="top:50px">
      <span class="cell c-name">Resume&amp;CV</span>
      <span class="cell c-date">23/02/2024</span>
      <span class="cell c-format">.ZIP</span>
      <span class="cell c-cat">Resume</span>
      <span class="cell c-status"><span class="badge pending">Pending Review</span></span>
      <span class="cell btn-view">View</span>
    </div>
    <div class="row item" style="top:121px">
      <span class="cell c-name">MyPortfolio_1</span>
      <span class="cell c-date">23/02/2024</span>
      <span class="cell c-format">.PDF</span>
      <span class="cell c-cat">Portfolio</span>
      <span class="cell c-status"><span class="badge pending">Pending Review</span></span>
      <span class="cell btn-view">View</span>
    </div>
    <div class="row item" style="top:192px">
      <span class="cell c-name">Curriculum Vitae</span>
      <span class="cell c-date">12/01/2024</span>
      <span class="cell c-format">.ZIP</span>
      <span class="cell c-cat">Application</span>
      <span class="cell c-status"><span class="badge approved">Approved</span></span>
      <svg class="cell more" width="6" height="20" viewBox="0 0 6 20"><circle cx="3" cy="3" r="2" fill="#444a52"/><circle cx="3" cy="10" r="2" fill="#444a52"/><circle cx="3" cy="17" r="2" fill="#444a52"/></svg>
    </div>
    <div class="pager">
      <span class="page-btn" style="left:508px;width:72px">&#8249; Back</span>
      <span class="page-btn current" style="left:597px;width:38px">1</span>
      <span class="page-btn" style="left:652px;width:73px">Next &#8250;</span>
    </div>
  </section>
</div>
</body>
</html>
```